Clean business card with logo provided

I want a card that will stand out among the masses. I need the color and image to show professionalism and yet have a family appeal showing that I only deal with win/win scenarios. The back of the card will be used to take notes about the individual so I can use that in my database entry. I like modern design but need professionalism in it also. It needs to fit my "clean, safe, and affordable housing" motto. I need to be able to write on the file and update the card details for my employees.

Target Market(s)

Investors looking to make investment income through real estate

Industry/Entity Type

Real Estate

Contact Information for Business Card

Brent Kovalich
blank address, city, st, zip code
480-555-3174
brentkovalich@ridgeworthrentals.example
www.ridgeworthrentals.example

Font styles to use
Sans Serif

Requirements
Must have
• I would like the back of the card to have lines for info. example
• Met/Visited: Date:
• Interets:
Nice to have
• I want the cards color to match the logo background color. Font with details to be san serif and black. I want the card rectangular with square corners. Standard business card size. I would like to see cards designed with both images to see which i prefer more.

```html
<!DOCTYPE html>
<html lang="en">
<head>
<meta charset="utf-8">
<title>Ridgeworth Rentals LLC – Business Cards</title>
<link rel="stylesheet" href="https://fonts.googleapis.com/css2?family=Open+Sans:wght@400;600;700&display=swap">
<style>
  :root {
    --teal: #1fb4c6;
    --ink: #0b0b0b;
    --paper: #ffffff;
    --backdrop: #e9e6e1;
    --rule: #2a2a2a;
  }
  * { box-sizing: border-box; margin: 0; padding: 0; }
  html, body { width: 1200px; height: 950px; overflow: hidden; }
  body {
    background: var(--backdrop);
    font-family: "Open Sans", Arial, sans-serif;
    position: relative;
  }
  .card {
    position: absolute;
    left: 250px;
    width: 700px;
    height: 400px;
    overflow: hidden;
    box-shadow: 0 6px 18px rgba(0,0,0,.25);
  }
  .card-notes { top: 50px; background: var(--paper); }
  .card-contact { top: 500px; background: var(--ink); }
  .card svg.shapes { position: absolute; inset: 0; width: 100%; height: 100%; }

  .brand { position: absolute; text-align: center; }
  .brand-name {
    color: var(--teal);
    font-weight: 600;
    font-size: 25px;
    letter-spacing: .5px;
    white-space: nowrap;
    line-height: 1.2;
  }
  .brand-tagline {
    color: var(--teal);
    font-size: 10.5px;
    margin-top: 2px;
    white-space: nowrap;
  }
  .card-notes .brand { right: 60px; top: 105px; }

  .note-field {
    position: absolute;
    display: flex;
    align-items: flex-end;
    gap: 10px;
    color: var(--teal);
    font-weight: 700;
    font-size: 16px;
  }
  .note-field .line { flex: 1; border-bottom: 1.5px solid var(--rule); height: 1px; margin-bottom: 5px; }
  .field-date { left: 470px; right: 40px; top: 176px; }
  .field-met { left: 60px; right: 40px; top: 244px; }
  .field-interests { left: 60px; right: 40px; top: 294px; }
  .field-blank { left: 60px; right: 40px; top: 344px; }

  .card-contact .brand { left: 22px; top: 178px; }
  .divider { position: absolute; left: 335px; top: 110px; width: 1px; height: 150px; background: #555; }
  .contact { position: absolute; left: 355px; top: 92px; color: var(--paper); font-size: 15px; line-height: 1.55; }
  .contact .person { color: var(--teal); font-size: 22px; font-weight: 400; letter-spacing: .5px; margin-bottom: 4px; }
  .contact .label { color: var(--teal); font-weight: 600; }
  .contact .email { font-size: 14px; }
  .website { position: absolute; right: 20px; bottom: 22px; color: var(--ink); font-size: 14px; letter-spacing: .5px; }
</style>
</head>
<body>

<section class="card card-notes" aria-label="Notes side">
  <svg class="shapes" viewBox="0 0 700 400" preserveAspectRatio="none" aria-hidden="true">
    <path d="M0,0 H700 V30 C560,40 360,80 0,200 Z" fill="var(--teal)"/>
    <path d="M0,200 C360,80 560,40 700,30 V34 C560,52 360,100 0,218 Z" fill="var(--ink)"/>
  </svg>
  <div class="brand">
    <div class="brand-name">Ridgeworth Rentals LLC</div>
    <div class="brand-tagline">Providing clean, safe, and affordable housing</div>
  </div>
  <div class="note-field field-date"><span>DATE:</span><span class="line"></span></div>
  <div class="note-field field-met"><span>MET/VISITED:</span><span class="line"></span></div>
  <div class="note-field field-interests"><span>INTERETS:</span><span class="line"></span></div>
  <div class="note-field field-blank"><span class="line"></span></div>
</section>

<section class="card card-contact" aria-label="Contact side">
  <svg class="shapes" viewBox="0 0 700 400" preserveAspectRatio="none" aria-hidden="true">
    <path d="M700,230 C600,260 480,340 330,400 H700 Z" fill="var(--teal)"/>
    <path d="M120,400 C320,375 480,330 560,280 C470,350 320,390 190,400 Z" fill="var(--paper)"/>
  </svg>
  <div class="brand">
    <div class="brand-name">Ridgeworth Rentals LLC</div>
    <div class="brand-tagline">Providing clean, safe, and affordable housing</div>
  </div>
  <div class="divider"></div>
  <div class="contact">
    <div class="person">BRENT KOVALICH</div>
    <div>1420 Alder Creek Road</div>
    <div>Fairbanks, Alaska 99701</div>
    <div><span class="label">Phone :</span> 480-555-3174</div>
    <div class="email">brentkovalich@ridgeworthrentals.example</div>
  </div>
  <div class="website">www.ridgeworthrentals.example</div>
</section>

</body>
</html>
```